VFX Company Business Card Design Project

The Kestrel Works is a decentralized Visual Effects Studio servicing the television and feature film industries.
Project Brief:
Take our logo that was previously designed on Pencil Harbor and make a double sided business card.
Requirements:
- Card MUST be double sided.
- Front of card MUST have the yellow part of our logo against the dark grey background.
- Back of card is completely up to the designer.
- Back of card must include the complete company logo.
Please follow these File Preparation guidelines:
http://printnook.ca/infopage?file=filetype_en&s=PrintNook_new&lang=en
Business

```html
<!DOCTYPE html>
<html lang="en">
<head>
<meta charset="utf-8">
<title>The Kestrel Works – Business Card</title>
<link rel="stylesheet" href="https://fonts.googleapis.com/css2?family=Questrial&family=Source+Sans+3:wght@400;600&display=swap">
<style>
  :root {
    --backdrop: #e6cfae;
    --card: #2a2a2a;
    --slate: #5d6b6e;
    --cream: #eef3e4;
    --gold: #fcc42a;
    --ink: #f2f2f2;
    --label: #1c1c1c;
    --mark-grey: #6b7577;
  }
  html, body {
    margin: 0;
    padding: 0;
    overflow: hidden;
  }
  .sheet {
    position: relative;
    width: 1200px;
    height: 788px;
    background: var(--backdrop);
    overflow: hidden;
    font-family: "Questrial", sans-serif;
  }
  .side-label {
    position: absolute;
    width: 200px;
    margin-left: -100px;
    text-align: center;
    font-family: "Source Sans 3", sans-serif;
    font-size: 22px;
    color: var(--label);
  }
  .card {
    position: absolute;
    width: 525px;
    height: 300px;
    border-radius: 20px;
    background: var(--card);
    overflow: hidden;
    box-shadow: 0 3px 8px rgba(0,0,0,0.35);
  }
  .card--back { left: 338px; top: 78px; }
  .card--front-1 { left: 54px; top: 445px; }
  .card--front-2 { left: 622px; top: 445px; }

  .swoosh {
    position: absolute;
    left: 0; top: 0;
    width: 525px; height: 300px;
  }
  .company-name {
    position: absolute;
    margin: 0;
    white-space: nowrap;
    font-weight: 400;
  }
  .card--back .company-name {
    left: 30px; top: 30px;
    font-size: 34px;
    color: var(--mark-grey);
  }
  .contact {
    position: absolute;
    left: 37px; top: 134px;
    color: var(--ink);
    font-size: 13px;
    line-height: 1;
  }
  .contact__name {
    font-size: 20px;
    margin-bottom: 14px;
  }
  .contact__name small { font-size: 13px; letter-spacing: 0.5px; }
  .contact__line { margin-bottom: 8px; }
  .contact__line b {
    font-family: "Source Sans 3", sans-serif;
    font-weight: 600;
    font-style: italic;
  }
  .contact__address { line-height: 18px; margin-top: 2px; }
  .online {
    position: absolute;
    right: 16px; top: 250px;
    text-align: right;
    color: var(--ink);
    font-size: 13px;
    line-height: 20px;
  }
  .online b {
    font-family: "Source Sans 3", sans-serif;
    font-weight: 600;
    font-style: italic;
  }
  .web-url {
    position: absolute;
    left: 0; right: 0; top: 258px;
    text-align: center;
    color: var(--ink);
    font-size: 19px;
    letter-spacing: 3px;
  }
  .brand-lockup {
    position: absolute;
    left: 0; right: 0;
    display: flex;
    align-items: center;
    justify-content: center;
    gap: 16px;
  }
  .brand-dot {
    border-radius: 50%;
    flex: none;
  }
  .card--front-1 .brand-lockup { top: 112px; }
  .card--front-1 .brand-dot { width: 56px; height: 56px; background: var(--gold); }
  .card--front-1 .company-name { position: static; font-size: 40px; color: var(--gold); }
  .card--front-2 .brand-lockup { top: 126px; }
  .card--front-2 .brand-dot { width: 44px; height: 44px; background: var(--gold); }
  .card--front-2 .company-name { position: static; font-size: 32px; color: var(--mark-grey); }
</style>
</head>
<body>
<main class="sheet">
  <div class="side-label" style="left:600px; top:32px;">Back</div>
  <div class="side-label" style="left:327px; top:403px;">Front - 1</div>
  <div class="side-label" style="left:900px; top:403px;">Front - 2</div>

  <section class="card card--back">
    <svg class="swoosh" viewBox="0 0 525 300" aria-hidden="true">
      <path d="M0,268 C200,292 392,252 525,156 L525,300 L0,300 Z" fill="var(--slate)"/>
      <path d="M0,263 C200,288 388,246 525,150 L525,158 C390,254 200,294 0,270 Z" fill="#151515"/>
      <path d="M0,260 C200,282 380,228 525,112 L525,150 C388,246 200,288 0,263 Z" fill="var(--cream)"/>
    </svg>
    <h1 class="company-name">The Kestrel Works</h1>
    <div class="contact">
      <div class="contact__name">Your Name, <small>Designation</small></div>
      <div class="contact__line"><b>cell</b> 123-456-7890</div>
      <div class="contact__line"><b>phone</b> 123-456-7890</div>
      <div class="contact__address">0000#, Area Name<br>State Name, Country code</div>
    </div>
    <div class="online">
      <div><b>email</b> info@kestrelworks.net</div>
      <div><b>web</b> www.kestrelworks.net</div>
    </div>
  </section>

  <section class="card card--front-1">
    <div class="brand-lockup">
      <span class="brand-dot"></span>
      <h2 class="company-name">The Kestrel Works</h2>
    </div>
    <div class="web-url">www.kestrelworks.net</div>
  </section>

  <section class="card card--front-2">
    <div class="brand-lockup">
      <span class="brand-dot"></span>
      <h2 class="company-name">The Kestrel Works</h2>
    </div>
    <div class="web-url">www.kestrelworks.net</div>
  </section>
</main>
</body>
</html>
```